Business Card Design

We are a commercial real estate brokerage in San Francisco, leasing office buildings downtown.
I would like a clean, elegant look. Simple but powerful .

Industry/Entity Type

Business

Contact Information for Business Card

Derek Holloway
lic# 07258143
415.555.0172
derek@velt-commercial.example
velt-commercial.example

```html
<!DOCTYPE html>
<html lang="en">
<head>
<meta charset="utf-8">
<title>Velt Commercial – Business Cards</title>
<link href="https://fonts.googleapis.com/css2?family=Arimo:wght@400;700&display=swap" rel="stylesheet">
<style>
  :root {
    --backdrop: #2e2e30;
    --card-back: #6b6b6d;
    --card-front: #ffffff;
    --brand-blue: #72809c;
    --text-dark: #444446;
    --text-light: #f2f2f2;
    --art-light: #d9d9db;
    --art-mid: #9c9c9f;
    --art-dark: #4a4a4d;
  }
  * { box-sizing: border-box; margin: 0; padding: 0; }
  html, body { width: 1200px; height: 950px; overflow: hidden; }
  body {
    background: var(--backdrop);
    font-family: "Arimo", Arial, sans-serif;
    position: relative;
  }
  .card {
    position: absolute;
    width: 700px;
    height: 400px;
    left: 250px;
    overflow: hidden;
    box-shadow: 0 6px 18px rgba(0,0,0,.45);
  }
  .card--back { top: 55px; background: var(--card-back); color: var(--text-light); }
  .card--front { top: 495px; background: var(--card-front); color: var(--text-dark); }

  .brand {
    display: flex;
    align-items: center;
    gap: 14px;
  }
  .brand__mark { width: 34px; height: 34px; flex: none; }
  .brand__name {
    font-weight: 700;
    font-size: 30px;
    letter-spacing: 1px;
    line-height: 1;
    text-transform: uppercase;
  }

  .card--back .brand {
    position: absolute;
    top: 130px;
    left: 0; right: 0;
    justify-content: center;
  }
  .card--back .brand__mark { background: var(--text-light); }
  .card--back .brand__name { color: var(--text-light); }
  .tagline {
    position: absolute;
    top: 240px;
    left: 0; right: 0;
    text-align: center;
    font-size: 17px;
    line-height: 1.45;
    letter-spacing: .3px;
  }

  .card--front .brand { position: absolute; top: 118px; left: 44px; }
  .card--front .brand__mark { background: var(--brand-blue); }
  .card--front .brand__name { color: var(--brand-blue); font-size: 26px; }

  .contact { position: absolute; left: 44px; top: 212px; }
  .contact__name {
    color: var(--brand-blue);
    font-size: 26px;
    margin-bottom: 8px;
  }
  .contact__line {
    display: flex;
    align-items: center;
    gap: 10px;
    font-size: 17px;
    line-height: 1.65;
  }
  .contact__line svg { width: 15px; height: 15px; fill: var(--text-dark); flex: none; }

  .skyline-art {
    position: absolute;
    top: 0; right: 0;
    width: 330px;
    height: 400px;
    background: linear-gradient(160deg, var(--art-light) 0%, var(--art-mid) 55%, var(--art-dark) 100%);
  }
</style>
</head>
<body>

  <section class="card card--back">
    <div class="brand">
      <span class="brand__mark"></span>
      <span class="brand__name">Velt Commercial</span>
    </div>
    <p class="tagline">commercial real estate brokerage in San Francisco<br>leasing office buildings downtown.</p>
  </section>

  <section class="card card--front">
    <div class="brand">
      <span class="brand__mark"></span>
      <span class="brand__name">Velt Commercial</span>
    </div>

    <div class="contact">
      <p class="contact__name">Derek Holloway</p>
      <p class="contact__line">lic# 07258143</p>
      <p class="contact__line">
        <svg viewBox="0 0 16 16" aria-hidden="true"><path d="M3 1l3 3-2 2c1 2 3 4 5 5l2-2 3 3-2 3C6 14 2 10 1 3z"/></svg>
        415.555.0172
      </p>
      <p class="contact__line">
        <svg viewBox="0 0 16 16" aria-hidden="true"><path d="M1 3h14v10H1z M2 4l6 5 6-5" fill="none" stroke="#444446" stroke-width="1.6"/></svg>
        derek@velt-commercial.example
      </p>
      <p class="contact__line">
        <svg viewBox="0 0 16 16" aria-hidden="true"><path d="M8 0a6 6 0 0 0-6 6c0 4 6 10 6 10s6-6 6-10a6 6 0 0 0-6-6zm0 8.5A2.5 2.5 0 1 1 8 3.5a2.5 2.5 0 0 1 0 5z"/></svg>
        velt-commercial.example
      </p>
    </div>

    <div class="skyline-art" role="img" aria-label="Greyscale illustration of downtown office towers"></div>
  </section>

</body>
</html>
```